Construction material supplies company business card ****

1. Full company name “K T Masonry Works Ltd”
I am after a Business card design for the company as a whole. We are better known in Solomon Islands as “K T Masonry” for short.

We are a building materials supplier of
Ready Mixed Concrete, Bricks and Blocks,
Quarry products- gravel, aggregates, sand etc.
Cement distributor/retailer of reputable brands.
Other prefab concrete products. Culverts, wave breakers, concrete retaining blocks etc.

2. Competitive Advantage over Competition: Quality, efficient, professional, dependable, reliable

3. We want people to feel trust worthy, high quality, strong when they see our brand

5. No preference to color. Maybe more sturdy and corporate. Not fancy.

Industry/Entity Type

CONSTRUCTION SUPPLY

Contact Information for Business Card

Name, Position, office phone mob phone, email

Requirements
Must have
• the company logo
Nice to have
• would like to see a mixture of designs, of with logo only and also with simple graphic designs to bring out the company whilst still have the strong sturdy professional feeling

```html
<!DOCTYPE html>
<html lang="en">
<head>
<meta charset="utf-8">
<title>K T Masonry – Business Card</title>
<link href="https://fonts.googleapis.com/css2?family=Roboto:wght@400;500;700&display=swap" rel="stylesheet">
<style>
  :root {
    --backdrop: #2a2a2a;
    --card-light: #ececec;
    --card-mid: #dcdcdc;
    --navy: #143c62;
    --navy-deep: #12385c;
    --text-dark: #1f2f40;
    --tag-text: #e3e9f0;
    --front-mark: #a9adb1;
  }
  * { margin: 0; padding: 0; box-sizing: border-box; }
  html, body { width: 1200px; height: 1138px; overflow: hidden; }
  body {
    background: var(--backdrop);
    font-family: "Roboto", Arial, sans-serif;
    position: relative;
  }
  .card {
    position: absolute;
    width: 620px;
    height: 375px;
    border-radius: 18px;
    overflow: hidden;
    background: radial-gradient(ellipse at 40% 35%, var(--card-light) 0%, var(--card-mid) 100%);
  }
  .card--front { left: 274px; top: 186px; }
  .card--back { left: 276px; top: 608px; }

  /* Front */
  .front-name {
    position: absolute;
    left: 0; right: 0; top: 136px;
    text-align: center;
    font-weight: 700;
    font-size: 48px;
    color: var(--front-mark);
    letter-spacing: 1px;
  }
  .front-web {
    position: absolute;
    left: 0; right: 0; top: 332px;
    text-align: center;
    font-size: 16px;
    font-weight: 500;
    letter-spacing: 9px;
    color: var(--navy);
  }

  /* Back */
  .brand-name {
    position: absolute;
    left: 70px; top: 140px;
    width: 200px;
    text-align: center;
    font-weight: 700;
    font-size: 30px;
    line-height: 1.15;
    color: var(--navy);
  }
  .person {
    position: absolute;
    left: 312px; top: 60px;
  }
  .person-name {
    font-size: 24px;
    font-weight: 700;
    color: var(--navy);
    line-height: 1.2;
  }
  .person-role {
    font-size: 16px;
    color: var(--navy);
    margin-top: 2px;
  }
  .contacts {
    position: absolute;
    left: 312px; top: 134px;
    list-style: none;
    font-size: 16px;
    color: var(--navy);
  }
  .contacts li {
    height: 26px;
    line-height: 26px;
    display: flex;
    align-items: center;
  }
  .contacts .icon {
    width: 14px; height: 14px;
    margin-right: 18px;
    flex: none;
  }
  .contacts .address { padding-left: 0; }
  .rule {
    position: absolute;
    left: 0; right: 0; top: 322px;
    height: 5px;
    background: var(--navy);
  }
  .tagline-band {
    position: absolute;
    left: 0; right: 0; top: 334px; bottom: 0;
    background: var(--navy-deep);
    color: var(--tag-text);
    font-size: 17px;
    display: flex;
    align-items: center;
    justify-content: center;
    word-spacing: 2px;
  }
</style>
</head>
<body>

  <section class="card card--front">
    <div class="front-name">K T Masonry</div>
    <div class="front-web">www.ktmasonry.com</div>
  </section>

  <section class="card card--back">
    <div class="brand-name">K T Masonry</div>

    <div class="person">
      <div class="person-name">Daniel Hughes</div>
      <div class="person-role">Managing Director</div>
    </div>

    <ul class="contacts">
      <li>
        <svg class="icon" viewBox="0 0 16 16" aria-hidden="true"><path fill="#143c62" d="M2 5c0-2 3-3 6-3s6 1 6 3v1h-3V5H5v1H2zM4 7h8l2 6H2z"/></svg>
        000 0000 0000
      </li>
      <li>
        <svg class="icon" viewBox="0 0 16 16" aria-hidden="true"><rect x="1" y="3" width="14" height="10" fill="#143c62"/><path d="M1.5 3.5L8 9l6.5-5.5" stroke="#e6e6e6" stroke-width="1.3" fill="none"/></svg>
        daniel@ktmasonry.com
      </li>
      <li>
        <svg class="icon" viewBox="0 0 16 16" aria-hidden="true"><circle cx="8" cy="8" r="6.5" fill="#143c62"/><path d="M1.5 8h13M8 1.5v13M3 4.5h10M3 11.5h10" stroke="#e6e6e6" stroke-width="0.9" fill="none"/><ellipse cx="8" cy="8" rx="3" ry="6.5" stroke="#e6e6e6" stroke-width="0.9" fill="none"/></svg>
        www.ktmasonry.com
      </li>
      <li class="address">18 Harbour Rd., Point Cruz,</li>
      <li class="address">Honiara, SB 00000</li>
    </ul>

    <div class="rule"></div>
    <div class="tagline-band">Quality &nbsp;|&nbsp; Efficient &nbsp;|&nbsp; Professional &nbsp;|&nbsp; Dependable &nbsp;|&nbsp; Reliable</div>
  </section>

</body>
</html>
```